Business cards - BRENT Roofing & Siding

We need simple business cards made up for our Roofing & Siding business based in Calgary Alberta.
The logo on one side of the card and potentially our slogan "Laid with care, proven by seasons".
The other side could have:
-A small logo
-Rep name:
-Rep cell phone:
-Rep email:
-Office phone: 403-684-2093
-Website: PrairieShingleWorks.com

We would like to incorporate the colours from our logo, especially the lite blue on the jpeg file. I have attached the ai file and jpeg file. We like the colours better on the jpeg file.

I do not require a money back guarantee

```html
<!DOCTYPE html>
<html lang="en">
<head>
<meta charset="utf-8">
<title>BRENT Roofing &amp; Siding – Business Cards</title>
<link rel="stylesheet" href="https://fonts.googleapis.com/css2?family=Lato:wght@400;700&display=swap">
<style>
  :root {
    --backdrop: #1e1e1e;
    --card: #ffffff;
    --blue-deep: #0565b4;
    --blue-mid: #1b78c2;
    --blue-lite: #0a8bef;
    --ink: #141414;
    --red: #e2231a;
  }
  * { margin: 0; padding: 0; box-sizing: border-box; }
  html, body {
    width: 1200px; height: 1200px; overflow: hidden;
    background: var(--backdrop);
    font-family: "Lato", sans-serif;
  }
  .card {
    position: absolute; left: 250px;
    width: 700px; height: 400px;
    background: var(--card);
    border-radius: 22px;
    overflow: hidden;
  }
  .card--front { top: 170px; }
  .card--back { top: 631px; }

  .card__art { position: absolute; inset: 0; }

  .brand-small {
    position: absolute; left: 48px; top: 70px;
    display: flex; align-items: center; gap: 12px;
  }
  .brand-mark { width: 22px; height: 22px; background: var(--blue-lite); }
  .brand-name {
    font-weight: 700; color: var(--ink);
    font-size: 22px; letter-spacing: 1.5px; line-height: 1.25;
  }

  .rep {
    position: absolute; right: 44px; top: 160px;
    text-align: right; color: #fff;
  }
  .rep__name { font-size: 30px; font-weight: 700; letter-spacing: 0.2px; line-height: 1; }
  .rep__title { font-size: 19px; margin-top: 6px; }
  .contacts { list-style: none; margin-top: 18px; }
  .contacts li {
    font-size: 16.5px; line-height: 23.5px;
    display: flex; justify-content: flex-end; align-items: center; gap: 10px;
  }
  .contacts svg { width: 14px; height: 14px; flex: none; }
  .rep__address { font-size: 16.5px; margin-top: 14px; white-space: nowrap; }

  .brand-large {
    position: absolute; left: 0; right: 0; top: 120px;
    display: flex; flex-direction: column; align-items: center; gap: 14px;
  }
  .brand-large .brand-mark { width: 40px; height: 40px; }
  .brand-large .brand-name { font-size: 44px; letter-spacing: 4px; text-align: center; }

  .slogan {
    position: absolute; left: 0; right: 0; top: 344px;
    display: flex; justify-content: center; align-items: center; gap: 6px;
    font-size: 18px; font-weight: 700; color: var(--blue-deep);
  }
  .slogan__rule { width: 46px; height: 1px; background: var(--red); }
  .slogan .lite { color: var(--blue-lite); }
</style>
</head>
<body>

<section class="card card--front">
  <svg class="card__art" viewBox="0 0 700 400" aria-hidden="true">
    <polygon points="150,400 550,0 700,0 700,400" fill="var(--blue-deep)"/>
    <polygon points="520,42 598,120 315,392 150,392" fill="var(--blue-mid)" opacity="0.7"/>
    <polygon points="525,0 700,0 700,182" fill="var(--blue-mid)" opacity="0.8"/>
    <line x1="110" y1="400" x2="510" y2="0" stroke="var(--blue-lite)" stroke-width="5"/>
    <line x1="124" y1="400" x2="524" y2="0" stroke="var(--blue-lite)" stroke-width="5"/>
  </svg>

  <div class="brand-small">
    <span class="brand-mark"></span>
    <span class="brand-name">BRENT<br>Roofing &amp; Siding</span>
  </div>

  <div class="rep">
    <h1 class="rep__name">DANIEL KOWALSKI</h1>
    <p class="rep__title">Managing Director</p>
    <ul class="contacts">
      <li>403-684-2093
        <svg viewBox="0 0 16 16"><path d="M4 1l3 3-2 2c1 2 3 4 5 5l2-2 3 3-2 3C7 15 1 9 1 3z" fill="#fff"/></svg></li>
      <li>403-684-2093
        <svg viewBox="0 0 16 16"><rect x="4" y="1" width="8" height="14" rx="1.5" fill="none" stroke="#fff" stroke-width="1.8"/><circle cx="8" cy="12" r="1" fill="#fff"/></svg></li>
      <li>daniel@prairieshingleworks.com
        <svg viewBox="0 0 16 16"><rect x="1" y="3" width="14" height="10" fill="#fff"/><path d="M1 3l7 6 7-6" fill="none" stroke="var(--blue-deep)" stroke-width="1.4"/></svg></li>
      <li>PrairieShingleWorks.com
        <svg viewBox="0 0 16 16"><circle cx="8" cy="8" r="6.5" fill="none" stroke="#fff" stroke-width="1.8"/><path d="M2 8h12M8 1.5c3 3 3 10 0 13M8 1.5c-3 3-3 10 0 13" fill="none" stroke="#fff" stroke-width="1.2"/></svg></li>
    </ul>
    <p class="rep__address">4820 - 9 Avenue S.E. Calgary, Alberta T2A 3K7</p>
  </div>
</section>

<section class="card card--back">
  <div class="brand-large">
    <span class="brand-mark"></span>
    <span class="brand-name">BRENT<br>Roofing &amp; Siding</span>
  </div>
  <p class="slogan">
    <span class="slogan__rule"></span>
    <span>LAID WITH CARE, <span class="lite">PROVEN BY SEASONS</span></span>
    <span class="slogan__rule"></span>
  </p>
</section>

</body>
</html>
```